BRISKLY sparkling water needs new artwork! Based in Southern California

"Briskly" is a new sparkling water company based in Southern California that offers refreshing flavors (lime, cherry, & mango) with B vitamins and antioxidants.

We would like to see packaging designs for standard 12oz cans for each of the three flavors.
Our initial preference is to have individual artwork for each flavor.

Attached are examples of competitors' designs.
Updates

We are extending the deadline for the Thanksgiving Holiday. Thank you all for your contributions.

```html
<!DOCTYPE html>
<html lang="en">
<head>
<meta charset="utf-8">
<title>Briskly Sparkling Water – Mango Can Label</title>
<link rel="stylesheet" href="https://fonts.googleapis.com/css2?family=Fredoka:wght@600&family=Londrina+Solid:wght@400;900&display=swap">
<style>
  :root {
    --page-bg: #f4f2f0;
    --label-pink: #d3204f;
    --label-pink-light: #e04a73;
    --label-pink-deep: #b8173f;
    --sunny-yellow: #f3d53d;
    --cloud-white: #ffffff;
    --headline-pink: #d42e62;
    --ink-teal: #244544;
  }
  * { box-sizing: border-box; margin: 0; padding: 0; }
  html, body {
    width: 900px;
    height: 1200px;
    overflow: hidden;
    background: var(--page-bg);
  }
  .canvas {
    position: relative;
    width: 900px;
    height: 1200px;
  }
  .can-label {
    position: absolute;
    left: 140px;
    top: 30px;
    width: 620px;
    height: 1140px;
    background: var(--label-pink);
    overflow: hidden;
  }
  .fruit-pattern {
    position: absolute;
    inset: 0;
    background: radial-gradient(ellipse at 50% 40%, var(--label-pink-light) 0%, var(--label-pink) 55%, var(--label-pink-deep) 100%);
    opacity: 0.7;
  }
  .brand-name {
    position: absolute;
    top: 200px;
    left: 0;
    width: 100%;
    text-align: center;
    font-family: "Fredoka", sans-serif;
    font-weight: 600;
    font-size: 96px;
    line-height: 1;
    color: var(--sunny-yellow);
    letter-spacing: 1px;
  }
  .headline-cloud {
    position: absolute;
    top: 335px;
    left: 65px;
    width: 490px;
    height: 335px;
  }
  .headline-cloud svg { width: 100%; height: 100%; display: block; }
  .headline {
    position: absolute;
    top: 372px;
    left: 65px;
    width: 490px;
    text-align: center;
    font-family: "Londrina Solid", sans-serif;
    font-weight: 400;
    color: var(--headline-pink);
    line-height: 1;
  }
  .headline-line-1 { display: block; font-size: 94px; letter-spacing: 1px; }
  .headline-line-2 { display: block; font-size: 140px; letter-spacing: 2px; margin-top: -4px; }
  .benefit-band {
    position: absolute;
    top: 655px;
    left: 110px;
    width: 400px;
    height: 34px;
    background: var(--sunny-yellow);
    font-family: "Londrina Solid", sans-serif;
    font-size: 18px;
    line-height: 34px;
    text-align: center;
    color: var(--ink-teal);
    letter-spacing: 0.5px;
  }
  .flavor-bubble {
    position: absolute;
    top: 735px;
    left: 300px;
    width: 260px;
    height: 150px;
  }
  .flavor-bubble svg { position: absolute; inset: 0; width: 100%; height: 100%; }
  .flavor-name {
    position: absolute;
    top: 14px;
    left: 0;
    width: 100%;
    text-align: center;
    font-family: "Londrina Solid", sans-serif;
    color: var(--ink-teal);
    line-height: 0.95;
  }
  .flavor-name-main { display: block; font-size: 60px; font-weight: 900; }
  .flavor-name-sub { display: block; font-size: 34px; font-weight: 400; }
  .net-volume {
    position: absolute;
    top: 935px;
    right: 70px;
    font-family: "Londrina Solid", sans-serif;
    font-size: 26px;
    color: var(--cloud-white);
    letter-spacing: 0.5px;
  }
</style>
</head>
<body>
<main class="canvas">
  <section class="can-label">
    <div class="fruit-pattern" role="img" aria-label="Faint line drawings of mangoes and leaves scattered across the label"></div>

    <div class="brand-name">Briskly</div>

    <div class="headline-cloud" aria-hidden="true">
      <svg viewBox="0 0 410 395" preserveAspectRatio="none">
        <path fill="var(--cloud-white)" d="M30 60 Q40 20 90 30 Q120 0 165 22 Q205 2 245 24 Q290 0 325 30 Q380 18 385 70 Q410 110 392 160 Q410 220 395 280 Q408 340 370 372 Q330 395 290 380 Q250 395 205 382 Q160 395 120 380 Q70 395 40 370 Q5 340 18 285 Q0 225 15 165 Q0 105 30 60 Z"/>
      </svg>
    </div>

    <h1 class="headline">
      <span class="headline-line-1">SPARKLING</span>
      <span class="headline-line-2">WATER</span>
    </h1>

    <p class="benefit-band">WITH B VITAMINS AND ANTIOXIDANTS</p>

    <div class="flavor-bubble">
      <svg viewBox="0 0 260 150" preserveAspectRatio="none" aria-hidden="true">
        <path fill="var(--sunny-yellow)" d="M20 12 L250 4 Q258 4 256 14 L246 112 Q245 122 234 122 L70 126 L28 148 L40 126 L22 126 Q10 126 10 114 L8 24 Q8 12 20 12 Z"/>
      </svg>
      <p class="flavor-name">
        <span class="flavor-name-main">MANGO</span>
        <span class="flavor-name-sub">FLAVOR</span>
      </p>
    </div>

    <p class="net-volume">12oz (355mL)</p>
  </section>
</main>
</body>
</html>
```